Modern Business Card

Modern professional business card with more than just logo and demographic info. Something memorable.

We are a trendy/modern chiropractic group with an emphasis on neurology, hence the minimalist-type brain logo. We want to convey that modern and technical aspect with professionalism and the elite nature of our practice environment.

```html
<!DOCTYPE html>
<html lang="en">
<head>
<meta charset="utf-8">
<title>Keystone Spine – Business Card</title>
<link href="https://fonts.googleapis.com/css2?family=Lato:wght@400;700&display=swap" rel="stylesheet">
<style>
  :root {
    --page: #ffffff;
    --card: #ffffff;
    --card-edge: #e6e6e6;
    --brand-blue: #4a7fc4;
    --brand-tint: #eef1f9;
    --ink: #161616;
    --ink-soft: #555555;
  }
  html, body {
    margin: 0;
    padding: 0;
    width: 1200px;
    height: 1200px;
    overflow: hidden;
    background: var(--page);
    font-family: "Lato", Arial, sans-serif;
  }
  .canvas { position: relative; width: 1200px; height: 1200px; }
  .card {
    position: absolute;
    background: var(--card);
    border: 1px solid var(--card-edge);
    box-sizing: border-box;
    overflow: hidden;
  }
  .card--front { left: 232px; top: 173px; width: 705px; height: 407px; }
  .card--back  { left: 231px; top: 628px; width: 703px; height: 400px; }

  .card__backdrop {
    position: absolute;
    right: -40px;
    top: 10px;
    width: 390px;
    height: 390px;
    border-radius: 50%;
    background: var(--brand-tint);
  }
  .brand { position: absolute; display: flex; align-items: center; }
  .brand__mark { background: var(--brand-blue); flex: none; }
  .brand__name {
    font-weight: 700;
    color: var(--ink);
    letter-spacing: 1px;
    line-height: 1;
    white-space: nowrap;
  }
  .card--front .brand { left: 40px; top: 50px; gap: 16px; }
  .card--front .brand__mark { width: 48px; height: 48px; }
  .card--front .brand__name { font-size: 36px; }

  .card--back .brand { left: 0; right: 0; top: 0; bottom: 0; justify-content: center; gap: 26px; }
  .card--back .brand__mark { width: 96px; height: 96px; }
  .card--back .brand__name { font-size: 64px; }

  .holder {
    position: absolute;
    left: 40px;
    right: 40px;
    top: 248px;
    display: flex;
    justify-content: space-between;
    align-items: flex-end;
    padding-bottom: 8px;
    border-bottom: 2px solid var(--brand-blue);
  }
  .holder__name { color: var(--brand-blue); font-size: 28px; font-weight: 400; letter-spacing: 0.3px; }
  .holder__title { color: var(--ink); font-size: 20px; letter-spacing: 0.3px; }

  .contact {
    position: absolute;
    left: 39px;
    top: 306px;
    color: var(--ink-soft);
    font-size: 19px;
    line-height: 32px;
    white-space: nowrap;
  }
  .contact__sep {
    display: inline-block;
    width: 2px;
    height: 15px;
    background: var(--brand-blue);
    margin: 0 5px;
    vertical-align: -1px;
  }
</style>
</head>
<body>
<div class="canvas">
  <section class="card card--front">
    <div class="card__backdrop"></div>
    <div class="brand">
      <span class="brand__mark"></span>
      <span class="brand__name">KEYSTONE SPINE</span>
    </div>
    <div class="holder">
      <span class="holder__name">MARLO FENWICK</span>
      <span class="holder__title">PRESIDENT</span>
    </div>
    <div class="contact">
      <div>555 0142 7781<span class="contact__sep"></span>555 0142 7781<span class="contact__sep"></span>hello@keystonespine.com</div>
      <div>48 Harbor Lane, Suite 2, Fairview 5551<span class="contact__sep"></span>www.keystonespine.com</div>
    </div>
  </section>

  <section class="card card--back">
    <div class="brand">
      <span class="brand__mark"></span>
      <span class="brand__name">KEYSTONE SPINE</span>
    </div>
  </section>
</div>
</body>
</html>
```